Business card for my new company (Accounting firm)

I need a business card for my new business Brightwell Advisory and Ledger SA. Our services are accounting, tax, audit and financial management. Our customers are small companies, start-ups and new companies. The final design has to show financial security, trust and growth. Please find our logo attached to the business card. Text for the business card: Brightwell Advisory and Ledger SA Tomas Varenholt Director and Founder Certified Accountant Tel. 022 418 57 34 tv@clairevalconseil.ch www.clairevalconseil.ch Rue des Vergières 27 1201 Geneva
Target Market(s)
Our customers are small companies, start-ups and new companies.
Industry/Entity Type
Finance And Accounting
Contact Information for Business Card
Claireval Conseil et Comptes SA
Tomas Varenholt
Directeur et Fondateur
Expert-comptable diplômé
Tél. 022 418 57 34
tv@clairevalconseil.ch
www.clairevalconseil.ch
Rue des Vergières 27
1201 Genève

```html
<!DOCTYPE html>
<html lang="fr">
<head>
<meta charset="utf-8">
<title>Claireval Conseil et Comptes SA – Carte de visite</title>
<link rel="stylesheet" href="https://fonts.googleapis.com/css2?family=Poppins:wght@400;500;600&display=swap">
<style>
  :root {
    --page-bg: #e9e9e9;
    --card-white: #f3f3f4;
    --brand-blue: #2aa0d4;
    --back-blue: #29a0d1;
    --pattern-blue: #2ea7d8;
    --ink: #3a3a3c;
    --ink-dark: #3b3b3d;
    --rule: #5a5a5c;
  }
  * { box-sizing: border-box; margin: 0; padding: 0; }
  html, body {
    width: 1105px;
    height: 1200px;
    overflow: hidden;
    background: var(--page-bg);
    font-family: "Poppins", sans-serif;
  }
  .canvas {
    position: relative;
    width: 1105px;
    height: 1200px;
  }
  .card {
    position: absolute;
    left: 182px;
    width: 747px;
    height: 427px;
  }
  .card-front {
    top: 118px;
    background: var(--card-white);
    color: var(--ink);
  }
  .brand-name {
    position: absolute;
    right: 42px;
    top: 172px;
    font-size: 38px;
    font-weight: 600;
    letter-spacing: 2px;
    line-height: 1;
    color: var(--ink-dark);
  }
  .person {
    position: absolute;
    left: 37px;
    top: 226px;
  }
  .person-name {
    font-size: 26px;
    font-weight: 500;
    color: var(--brand-blue);
    line-height: 1.2;
  }
  .person-role {
    font-size: 17.5px;
    font-weight: 400;
    line-height: 1.3;
  }
  .divider {
    position: absolute;
    left: 37px;
    right: 42px;
    top: 312px;
    height: 1px;
    background: var(--rule);
  }
  .contact-list {
    position: absolute;
    left: 37px;
    top: 326px;
    list-style: none;
    font-size: 17.5px;
    line-height: 21px;
  }
  .contact-list li {
    display: flex;
    align-items: center;
    gap: 9px;
  }
  .contact-icon {
    width: 14px;
    height: 14px;
    fill: var(--brand-blue);
    flex: none;
  }
  .address {
    position: absolute;
    right: 42px;
    top: 326px;
    text-align: right;
    font-style: normal;
    font-size: 17.5px;
    line-height: 21px;
  }
  .card-back {
    top: 635px;
    background: var(--back-blue);
    overflow: hidden;
  }
  .back-texture {
    position: absolute;
    inset: 0;
    background: linear-gradient(135deg, var(--back-blue), var(--pattern-blue));
  }
  .back-brand {
    position: absolute;
    right: 54px;
    bottom: 52px;
    font-size: 17px;
    font-weight: 600;
    letter-spacing: 1px;
    color: #ffffff;
  }
</style>
</head>
<body>
<main class="canvas">
  <section class="card card-front" aria-label="Recto de la carte">
    <div class="brand-name">CLAIREVAL</div>

    <div class="person">
      <h1 class="person-name">Tomas Varenholt</h1>
      <p class="person-role">Directeur et Fondateur</p>
      <p class="person-role">Expert-comptable diplômé</p>
    </div>

    <div class="divider"></div>

    <ul class="contact-list">
      <li>
        <svg class="contact-icon" viewBox="0 0 24 24" aria-hidden="true"><path d="M6.6 10.8c1.4 2.8 3.8 5.1 6.6 6.6l2.2-2.2c.3-.3.7-.4 1-.2 1.1.4 2.3.6 3.6.6.6 0 1 .4 1 1V20c0 .6-.4 1-1 1C10.6 21 3 13.4 3 4c0-.6.4-1 1-1h3.5c.6 0 1 .4 1 1 0 1.3.2 2.5.6 3.6.1.3 0 .7-.2 1l-2.3 2.2z"/></svg>
        <span>022 418 57 34</span>
      </li>
      <li>
        <svg class="contact-icon" viewBox="0 0 24 24" aria-hidden="true"><path d="M2 5h20v14H2z M3 6l9 7 9-7" /><path d="M2 5h20L12 12.5z" fill="#fff" opacity=".35"/></svg>
        <span>tv@clairevalconseil.ch</span>
      </li>
      <li>
        <svg class="contact-icon" viewBox="0 0 24 24" aria-hidden="true"><circle cx="12" cy="12" r="10"/><path d="M7 7c2 0 3 1 3 3s-2 2-2 4 2 2 2 4M15 4c0 2 2 3 3 3M14 14c1 0 2 1 2 3" stroke="#fff" stroke-width="1.6" fill="none"/></svg>
        <span>clairevalconseil.ch</span>
      </li>
    </ul>

    <address class="address">
      Claireval Conseil et Comptes SA<br>
      Rue des Vergières 27<br>
      1201 Genève
    </address>
  </section>

  <section class="card card-back" aria-label="Verso de la carte">
    <div class="back-texture" role="img" aria-label="Motif discret répété en bleu clair sur fond bleu"></div>
    <div class="back-brand">CLAIREVAL</div>
  </section>
</main>
</body>
</html>
```